Nivel Crest - Powerpoint Templates

We are a consultancy to help builders to optimize their planning in order to save building costs. For that reason we need templates for teasers and presentations where we offer our services, show our team and their capacities and present workflows, organization charts, price lists etc.

```html
<!DOCTYPE html>
<html lang="en">
<head>
<meta charset="utf-8">
<title>Nivel Crest – Presentation Templates</title>
<link href="https://fonts.googleapis.com/css2?family=Orbitron:wght@600;800&family=Poppins:wght@400;500;600&display=swap" rel="stylesheet">
<style>
:root{
  --gold:#c8923a;
  --gold-light:#e0ad55;
  --ink:#1d1f24;
  --night:#1b2431;
  --night-2:#2b3646;
  --paper:#ffffff;
  --canvas:#eeeeee;
  --muted:#555a63;
  --display:'Orbitron',sans-serif;
  --body:'Poppins',sans-serif;
}
*{box-sizing:border-box;margin:0;padding:0}
html,body{width:1200px;height:3656px;overflow:hidden;background:var(--canvas);font-family:var(--body);color:var(--ink)}
.deck{position:relative;width:1200px;height:3656px}
.slide{position:absolute;left:100px;width:1000px;height:562px;overflow:hidden;background:var(--paper);box-shadow:0 2px 8px rgba(0,0,0,.12)}
.s1{top:40px}.s2{top:638px}.s3{top:1236px}.s4{top:1834px}.s5{top:2432px}.s6{top:3030px}
.photo{position:absolute}
.title{font-family:var(--display);font-weight:800;color:var(--gold);text-transform:uppercase;letter-spacing:2px;line-height:1.05}
.copy{font-size:11px;line-height:1.6;color:var(--muted)}
.brand{font-family:var(--display);font-weight:800;text-transform:uppercase;letter-spacing:2px;color:#fff;display:flex;align-items:center;gap:10px}
.brand .mark{width:14px;height:14px;background:var(--gold)}
/* footer */
.footer{position:absolute;left:0;bottom:0;width:100%;height:40px}
.footer .band{position:absolute;left:0;bottom:0;width:100%;height:40px}
.footer .brand{position:absolute;left:22px;bottom:11px;font-size:12px;color:var(--gold)}
.footer .num{position:absolute;right:22px;bottom:9px;width:22px;height:22px;background:var(--ink);color:#fff;font-size:10px;display:flex;align-items:center;justify-content:center}
/* cover */
.s1 .photo{inset:0;background:linear-gradient(120deg,#3b3124 0%,#b78a45 45%,#6b5233 75%,#2a2520 100%)}
.s1 .shade{position:absolute;inset:0;background:linear-gradient(180deg,rgba(20,20,24,.15),rgba(20,20,24,.55))}
.s1 .brand{position:absolute;left:330px;top:210px;font-size:40px}
.s1 .brand .mark{width:34px;height:34px}
.s1 .headline{position:absolute;left:0;right:0;top:300px;text-align:center;font-family:var(--display);font-weight:600;color:#fff;font-size:22px;letter-spacing:2px;line-height:1.4}
/* about */
.s2 .title{position:absolute;left:42px;top:70px;font-size:40px}
.s2 .rule{position:absolute;left:42px;top:170px;width:90px;height:4px;background:var(--gold)}
.s2 .copy{position:absolute;left:42px;width:420px}
.s2 .p1{top:188px}.s2 .p2{top:316px}
.s2 .photo{right:0;top:0;width:470px;height:522px;background:linear-gradient(160deg,#d9dde2,#8e99a6 55%,#4b5563);clip-path:polygon(18% 0,100% 0,100% 100%,0 100%)}
/* services */
.s3{background:var(--night)}
.s3 .photo{inset:0;background:linear-gradient(135deg,#26303f 0%,#3c4a5e 50%,#1a2230 100%)}
.s3 .grid{position:absolute;left:36px;top:64px;display:grid;grid-template-columns:repeat(3,150px);gap:20px}
.card{background:#fff;height:160px;padding:18px 16px;border-top:4px solid var(--gold)}
.card h3{font-family:var(--display);font-size:13px;color:var(--gold);letter-spacing:1px;margin-bottom:10px}
.card p{font-size:10px;line-height:1.55;color:var(--muted)}
.s3 .title{position:absolute;left:620px;top:170px;font-size:40px}
.s3 .copy{position:absolute;left:620px;top:270px;width:330px;color:#d3d8e0}
/* team */
.s4 .title{position:absolute;left:0;right:0;top:34px;text-align:center;font-size:34px}
.s4 .intro{position:absolute;left:100px;right:100px;top:86px;text-align:center;font-size:10px}
.s4 .team{position:absolute;left:40px;top:140px;display:grid;grid-template-columns:repeat(3,292px);gap:22px 12px}
.member{height:140px;background:linear-gradient(90deg,var(--gold) 0 36%,#2a2a2e 36% 100%);display:flex;align-items:center;padding:0 14px;gap:16px}
.member .avatar{width:88px;height:88px;border-radius:50%;border:4px solid #fff;background:linear-gradient(160deg,#c9ccd1,#7c8591)}
.member h3{font-family:var(--display);font-size:12px;color:var(--gold);letter-spacing:1px;margin-bottom:8px}
.member p{font-size:10px;line-height:1.5;color:#e6e6e6;width:140px}
/* charts */
.s5 .title{position:absolute;left:42px;top:40px;font-size:36px}
.s5 .intro{position:absolute;left:42px;top:140px;width:420px}
.s5 .points{position:absolute;left:42px;top:230px;display:flex;flex-direction:column;gap:22px}
.point{display:flex;gap:16px;align-items:center}
.point .icon{width:46px;height:46px;border-radius:50%;background:#3a3d44;display:flex;align-items:center;justify-content:center}
.point h3{font-size:13px;font-weight:600;margin-bottom:2px}
.point p{font-size:9.5px;line-height:1.5;color:var(--muted);width:300px}
.s5 .chart{position:absolute;left:500px;top:40px}
/* thank you */
.s6{background:var(--night)}
.s6 .bg{position:absolute;inset:0;background:linear-gradient(135deg,#1c2533,#2b3646 60%,#1b2230)}
.s6 .photo{right:0;top:0;width:560px;height:562px;background:linear-gradient(150deg,#a9b4c2,#5d6b7e 55%,#2e3a4c);clip-path:polygon(22% 0,100% 0,100% 100%,0 100%)}
.s6 .title{position:absolute;left:42px;top:60px;font-size:44px;color:#fff}
.s6 .contacts{position:absolute;left:42px;top:160px;display:flex;flex-direction:column;gap:26px}
.contact{display:flex;gap:14px}
.contact .icon{width:30px;height:30px;background:var(--gold);display:flex;align-items:center;justify-content:center;flex:none}
.contact h3{font-size:18px;font-weight:600;color:var(--gold);line-height:1.2}
.contact p{font-size:12px;color:#fff;line-height:1.5}
.s6 .logo-band{position:absolute;right:0;bottom:40px;width:520px;height:110px;background:var(--gold);clip-path:polygon(12% 0,100% 0,100% 100%,0 100%);display:flex;align-items:center;justify-content:center}
.s6 .logo-band .brand{font-size:30px}
.s6 .logo-band .brand .mark{width:24px;height:24px;background:#fff}
</style>
</head>
<body>
<main class="deck">

  <section class="slide s1">
    <div class="photo" role="img" aria-label="Construction team in hard hats shaking hands on site"></div>
    <div class="shade"></div>
    <div class="brand"><span class="mark"></span>Nivel Crest</div>
    <p class="headline">NAM LIBERO TEMPORE, CUM SOLUTA NOBIS EST<br>ELIGENDI OPTIO CUMQUE</p>
  </section>

  <section class="slide s2">
    <h2 class="title">About<br>Nivel Crest</h2>
    <div class="rule"></div>
    <p class="copy p1">Sed ut perspiciatis unde omnis iste natus error sit voluptatem accusantium doloremque laudantium, totam rem aperiam, eaque ipsa quae ab illo inventore veritatis et quasi architecto beatae vitae dicta sunt explicabo. Nemo enim ipsam voluptatem quia voluptas sit aspernatur aut odit aut fugit, sed quia consequuntur magni dolores eos qui ratione voluptatem sequi nesciunt.</p>
    <p class="copy p2">Sed ut perspiciatis unde omnis iste natus error sit voluptatem accusantium doloremque laudantium, totam rem aperiam, eaque ipsa quae ab illo inventore veritatis et quasi architecto beatae vitae dicta sunt explicabo. Nemo enim ipsam voluptatem quia voluptas sit aspernatur aut odit aut fugit, sed quia consequuntur magni dolores eos qui ratione voluptatem sequi nesciunt.</p>
    <div class="photo" role="img" aria-label="Engineers and a client in a meeting in a modern building"></div>
    <footer class="footer">
      <svg class="band" viewBox="0 0 1000 40" preserveAspectRatio="none"><polygon points="0,40 1000,40 1000,8 240,8 220,0 0,0" fill="#1d1f24"/><polygon points="250,40 1000,40 1000,14 270,14" fill="#c8923a"/></svg>
      <div class="brand"><span class="mark"></span>Nivel Crest</div>
      <span class="num">2</span>
    </footer>
  </section>

  <section class="slide s3">
    <div class="photo" role="img" aria-label="Looking up at dark glass office towers"></div>
    <div class="grid">
      <article class="card"><h3>NEMO ENIM</h3><p>Neque porro quisquam est, qui dolorem ipsum quia dolor sit amet, consectetur.</p></article>
      <article class="card"><h3>NEMO ENIM</h3><p>Neque porro quisquam est, qui dolorem ipsum quia dolor sit amet, consectetur.</p></article>
      <article class="card"><h3>NEMO ENIM</h3><p>Neque porro quisquam est, qui dolorem ipsum quia dolor sit amet, consectetur.</p></article>
      <article class="card"><h3>NEMO ENIM</h3><p>Neque porro quisquam est, qui dolorem ipsum quia dolor sit amet, consectetur.</p></article>
      <article class="card"><h3>NEMO ENIM</h3><p>Neque porro quisquam est, qui dolorem ipsum quia dolor sit amet, consectetur.</p></article>
      <article class="card"><h3>NEMO ENIM</h3><p>Neque porro quisquam est, qui dolorem ipsum quia dolor sit amet, consectetur.</p></article>
    </div>
    <h2 class="title">Our<br>Services</h2>
    <p class="copy">Sed ut perspiciatis unde omnis iste natus error sit voluptatem accusantium doloremque laudantium, totam rem aperiam, eaque ipsa quae ab illo inventore veritatis et quasi architecto beatae vitae dicta sunt explicabo.</p>
    <footer class="footer">
      <svg class="band" viewBox="0 0 1000 40" preserveAspectRatio="none"><polygon points="0,40 1000,40 1000,34 0,34" fill="#c8923a"/></svg>
      <span class="num" style="background:#c8923a">3</span>
    </footer>
  </section>

  <section class="slide s4">
    <h2 class="title">Our Team</h2>
    <p class="copy intro">Sed ut perspiciatis unde omnis iste natus error sit voluptatem accusantium doloremque laudantium, totam rem aperiam, eaque ipsa quae ab illo inventore veritatis et quasi architecto beatae vitae dicta sunt explicabo.</p>
    <div class="team">
      <article class="member"><div class="avatar" role="img" aria-label="Team member portrait"></div><div><h3>NAME HEADING</h3><p>Excepteur sint occaecat cupidatat non proident.</p></div></article>
      <article class="member"><div class="avatar" role="img" aria-label="Team member portrait"></div><div><h3>NAME HEADING</h3><p>Excepteur sint occaecat cupidatat non proident.</p></div></article>
      <article class="member"><div class="avatar" role="img" aria-label="Team member portrait"></div><div><h3>NAME HEADING</h3><p>Excepteur sint occaecat cupidatat non proident.</p></div></article>
      <article class="member"><div class="avatar" role="img" aria-label="Team member portrait"></div><div><h3>NAME HEADING</h3><p>Excepteur sint occaecat cupidatat non proident.</p></div></article>
      <article class="member"><div class="avatar" role="img" aria-label="Team member portrait"></div><div><h3>NAME HEADING</h3><p>Excepteur sint occaecat cupidatat non proident.</p></div></article>
      <article class="member"><div class="avatar" role="img" aria-label="Team member portrait"></div><div><h3>NAME HEADING</h3><p>Excepteur sint occaecat cupidatat non proident.</p></div></article>
    </div>
    <footer class="footer">
      <svg class="band" viewBox="0 0 1000 40" preserveAspectRatio="none"><polygon points="0,40 1000,40 1000,8 240,8 220,0 0,0" fill="#1d1f24"/><polygon points="250,40 1000,40 1000,14 270,14" fill="#c8923a"/></svg>
      <div class="brand"><span class="mark"></span>Nivel Crest</div>
      <span class="num">4</span>
    </footer>
  </section>

  <section class="slide s5">
    <h2 class="title">Organization<br>Charts</h2>
    <p class="copy intro">Sed ut perspiciatis unde omnis iste natus error sit voluptatem accusantium doloremque laudantium, totam rem aperiam, eaque ipsa quae ab illo inventore veritatis.</p>
    <div class="points">
      <div class="point"><span class="icon"><svg width="20" height="20" viewBox="0 0 20 20"><path d="M4 10l4 4 8-8" stroke="#fff" stroke-width="2.4" fill="none"/></svg></span><div><h3>Sed ut perspiciatis unde</h3><p>Natus error sit voluptatem accusantium doloremque laudantium, totam rem aperiam, eaque ipsa quae ab illo.</p></div></div>
      <div class="point"><span class="icon"><svg width="20" height="20" viewBox="0 0 20 20"><path d="M4 10l4 4 8-8" stroke="#fff" stroke-width="2.4" fill="none"/></svg></span><div><h3>Sed ut perspiciatis unde</h3><p>Natus error sit voluptatem accusantium doloremque laudantium, totam rem aperiam, eaque ipsa quae ab illo.</p></div></div>
      <div class="point"><span class="icon"><svg width="20" height="20" viewBox="0 0 20 20"><path d="M4 10l4 4 8-8" stroke="#fff" stroke-width="2.4" fill="none"/></svg></span><div><h3>Sed ut perspiciatis unde</h3><p>Natus error sit voluptatem accusantium doloremque laudantium, totam rem aperiam, eaque ipsa quae ab illo.</p></div></div>
    </div>
    <svg class="chart" width="470" height="440" viewBox="0 0 470 440" font-family="Poppins, sans-serif" font-size="9" fill="#777">
      <g stroke="#e3e3e3">
        <line x1="40" y1="20" x2="460" y2="20"/><line x1="40" y1="65" x2="460" y2="65"/><line x1="40" y1="110" x2="460" y2="110"/><line x1="40" y1="155" x2="460" y2="155"/><line x1="40" y1="200" x2="460" y2="200"/><line x1="40" y1="245" x2="460" y2="245"/><line x1="40" y1="290" x2="460" y2="290"/><line x1="40" y1="335" x2="460" y2="335"/><line x1="40" y1="380" x2="460" y2="380"/><line x1="40" y1="420" x2="460" y2="420" stroke="#999"/>
      </g>
      <g text-anchor="end">
        <text x="34" y="23">90%</text><text x="34" y="68">80%</text><text x="34" y="113">70%</text><text x="34" y="158">60%</text><text x="34" y="203">50%</text><text x="34" y="248">40%</text><text x="34" y="293">30%</text><text x="34" y="338">20%</text><text x="34" y="383">10%</text><text x="34" y="423">0%</text>
      </g>
      <g fill="#c8923a">
        <rect x="52" y="260" width="18" height="160"/><rect x="104" y="220" width="18" height="200"/><rect x="156" y="110" width="18" height="310"/><rect x="208" y="160" width="18" height="260"/><rect x="260" y="250" width="18" height="170"/><rect x="312" y="190" width="18" height="230"/><rect x="364" y="150" width="18" height="270"/><rect x="416" y="70" width="18" height="350"/>
      </g>
      <g fill="#2f3137">
        <rect x="72" y="300" width="18" height="120"/><rect x="124" y="280" width="18" height="140"/><rect x="176" y="230" width="18" height="190"/><rect x="228" y="330" width="18" height="90"/><rect x="280" y="290" width="18" height="130"/><rect x="332" y="270" width="18" height="150"/><rect x="384" y="310" width="18" height="110"/><rect x="436" y="380" width="18" height="40"/>
      </g>
      <g text-anchor="middle"><text x="71" y="436">2017</text><text x="123" y="436">2018</text><text x="175" y="436">2019</text><text x="227" y="436">2020</text><text x="279" y="436">2021</text><text x="331" y="436">2022</text><text x="383" y="436">2023</text><text x="435" y="436">2024</text></g>
    </svg>
    <footer class="footer">
      <svg class="band" viewBox="0 0 1000 40" preserveAspectRatio="none"><polygon points="0,40 1000,40 1000,8 240,8 220,0 0,0" fill="#1d1f24"/><polygon points="250,40 1000,40 1000,14 270,14" fill="#c8923a"/></svg>
      <div class="brand"><span class="mark"></span>Nivel Crest</div>
      <span class="num">5</span>
    </footer>
  </section>

  <section class="slide s6">
    <div class="bg" role="img" aria-label="Dark city skyline at dusk"></div>
    <div class="photo" role="img" aria-label="Two businessmen shaking hands in an office"></div>
    <h2 class="title">Thank You!</h2>
    <div class="contacts">
      <div class="contact"><span class="icon"><svg width="16" height="16" viewBox="0 0 16 16"><path d="M8 1a5 5 0 0 0-5 5c0 4 5 9 5 9s5-5 5-9a5 5 0 0 0-5-5zm0 7a2 2 0 1 1 0-4 2 2 0 0 1 0 4z" fill="#fff"/></svg></span><div><h3>Address</h3><p>418 Halvern Ave. Suite 20<br>Dunmore, OR 97301, USA</p></div></div>
      <div class="contact"><span class="icon"><svg width="16" height="16" viewBox="0 0 16 16"><path d="M3 1h3l1.5 4-2 1.2a9 9 0 0 0 4.3 4.3L11 8.5l4 1.5v3a2 2 0 0 1-2 2A12 12 0 0 1 1 3a2 2 0 0 1 2-2z" fill="#fff"/></svg></span><div><h3>Phone</h3><p>+1 555-014-7720</p></div></div>
      <div class="contact"><span class="icon"><svg width="16" height="16" viewBox="0 0 16 16"><rect x="1" y="3" width="14" height="10" fill="#fff"/><path d="M1 3l7 6 7-6" stroke="#c8923a" stroke-width="1.4" fill="none"/></svg></span><div><h3>Email</h3><p>hello@nivelcrest.example</p></div></div>
    </div>
    <div class="logo-band"><div class="brand"><span class="mark"></span>Nivel Crest</div></div>
    <footer class="footer">
      <svg class="band" viewBox="0 0 1000 40" preserveAspectRatio="none"><polygon points="0,40 1000,40 1000,0 0,0" fill="#1d1f24"/></svg>
    </footer>
  </section>

</main>
</body>
</html>
```